Vensol Holdings Web Design

Vensol Holdings Limited Shenzhen

This project is a 10 page launch website.
Our client is seeking a contemporary homepage design for a Holdings company. Once we are happy with the homepage design and select designer we will request a secondary page design.

Please see attached company LOGO for an idea of style, it incorporates the traditional Chinese furniture lattice work. The Corvel crest website is one of our clients favorite so we would like to see a similar homepage design to this website.

Use the websites below for reference purpose. The first two are Chinese and the second two are international. We would like to see elements of both but more focus on international design.

http://www.evergrande.com/http://www.taurenfield.com/pub/default.aspx http://www.corvelcrest.com/zh/maldives_lorinhaven/
http://www.quelba-studio.com
http://media-cache-ex0.snapvalu.com/originals/71/a3/19/71a319c5b2d04e8f6a17c3b9e5d0f4a1.jpg

Company Background
VENSOL HOLDINGS, located in Qianhai, China, is a new real-estate project operator, structuring urban-rural real-estate investment and development, and industrial fund investment. The company also invests in supply chain management and supporting infrastructures. To create new spaces and livable cities Vensol Holdings develop win-win strategic partnerships with a number of institutions. Currently cooperating with Tianjing North Lumore, China urban and rural integrated demonstration.

Target Market(s)

B2B property investment. Target market customers are senior level management/decision makers of large corporations. Focusing geographically on the domestic market first and expanding internationally in 2nd and 3rd years.

Industry/Entity Type

Investment

Requirements
Must have
• Since this is a new company, we would like to the website representing growth and power, E.g. like a growing tree.
Should not have
• Low-level vectors such as curency symbols, American dollar.

```html
<!DOCTYPE html>
<html lang="en">
<head>
<meta charset="utf-8">
<title>Vensol Holdings</title>
<link href="https://fonts.googleapis.com/css2?family=Open+Sans:ital,wght@0,300;0,400;0,600;1,400&display=swap" rel="stylesheet">
<style>
:root{
  --gold:#b58a3a;
  --gold-light:#d9b15a;
  --gold-band:#b4954c;
  --gold-field:#9c7f3a;
  --ink:#333;
  --muted:#666;
  --dark:#2a2123;
  --footer:#242223;
  --white:#fff;
}
*{margin:0;padding:0;box-sizing:border-box}
html,body{width:845px;height:1200px;overflow:hidden;background:var(--white)}
body{position:relative;font-family:'Open Sans',sans-serif;color:var(--ink)}
.abs{position:absolute}

.site-header{left:0;top:0;width:845px;height:68px;background:var(--white);border-bottom:1px solid #ddd}
.brand{left:91px;top:0;width:99px;height:94px;background:var(--white);box-shadow:0 1px 4px rgba(0,0,0,.25);z-index:3;display:flex;align-items:center;justify-content:center}
.brand-name{font-size:11px;line-height:14px;color:var(--gold);font-weight:600;text-align:center}
.main-nav{top:47px;left:0;width:845px;height:12px}
.main-nav a{position:absolute;font-size:8.5px;color:#333;text-decoration:none;letter-spacing:.4px}

.hero{left:0;top:68px;width:845px;height:348px;background:linear-gradient(180deg,#4a86c8 0%,#8fb3d6 35%,#6a5b63 60%,#8a4a1f 80%,#2b1c12 100%)}
.hero-rule{left:0;top:416px;width:845px;height:4px;background:var(--gold-light)}
.hero-shadow{left:96px;top:420px;width:653px;height:16px;background:radial-gradient(ellipse at 50% 0%,rgba(0,0,0,.28),rgba(0,0,0,0) 70%)}
.hero-caption{left:91px;top:194px;width:437px;height:68px;background:rgba(255,255,255,.82);padding:7px 10px;font-size:15.5px;line-height:19px;font-weight:600;color:#222}
.hero-dots{left:91px;top:383px;display:flex;gap:7px}
.hero-dots span{width:14px;height:14px;border-radius:50%;background:rgba(255,255,255,.5)}
.hero-dots span:first-child{background:#fff}

.welcome{left:90px;top:450px;width:665px;text-align:center}
.welcome h1{font-size:18px;font-weight:400;color:#333}
.welcome h1 em,.gold-word{font-style:normal;color:var(--gold)}
.welcome p{margin-top:13px;font-size:9px;line-height:16.2px;font-weight:300;color:#555}

.news-bar{left:0;top:574px;width:845px;height:44px;background:#fff;box-shadow:0 -3px 6px rgba(0,0,0,.05),0 3px 6px rgba(0,0,0,.05)}
.news-icon{left:119px;top:591px;width:12px;height:12px;background:#e2762c;border-radius:2px}
.news-label{left:141px;top:587px;font-size:14.5px;color:#444}
.news-text{left:244px;top:592px;font-size:8.4px;color:#333}
.news-text a{color:var(--gold);font-style:italic;text-decoration:none}
.news-arrows{left:709px;top:591px}

.projects{left:0;top:636px;width:845px;height:300px;background:linear-gradient(180deg,#2e2426 0%,#1f1a1b 100%)}
.project-photo{left:92px;top:680px;width:379px;height:207px;border:1px solid #888;background:linear-gradient(135deg,#c9cfd6 0%,#8e98a2 40%,#4f6b3e 75%,#2b2b2b 100%)}
.slide-btn{width:26px;height:26px;border-radius:50%;top:771px}
.projects-title{left:506px;top:675px;font-size:17.5px;color:#fff;font-weight:400}
.project-item{left:507px;width:240px}
.project-item h3{font-size:10px;font-weight:600;color:var(--gold-light)}
.project-item p{margin-top:3px;font-size:8px;line-height:14.3px;color:#ddd}
.view-more{left:674px;top:862px;width:79px;height:25px;background:#fff;color:#333;font-size:9px;font-weight:600;display:flex;align-items:center;justify-content:center;letter-spacing:.3px}

.info{left:0;top:936px;width:845px;height:210px;background:var(--gold-band)}
.info-title{top:956px;font-size:17.5px;font-weight:400;color:#fff}
.about-text{left:91px;top:985px;width:215px;font-size:8px;line-height:16px;color:#2d2410}
.learn-more{left:92px;top:1107px;font-size:10px;font-weight:600;color:#2d2410;letter-spacing:.4px}
.service-list{left:334px;top:981px;list-style:none}
.service-list li{font-size:8px;color:#2d2410;height:24px;display:flex;align-items:center;gap:10px}
.service-list li::before{content:"\2192";font-size:8px}
.field{background:var(--gold-field);color:#f3ead6;font-size:9px;padding:0 11px;display:flex;align-items:center;border-radius:2px}
.field-msg{align-items:flex-start;padding-top:8px}
.send-btn{left:699px;top:1107px;width:54px;height:25px;background:#2a2426;color:#fff;font-size:9px;display:flex;align-items:center;justify-content:center;border-radius:2px}

.site-footer{left:0;top:1146px;width:845px;height:54px;background:var(--footer)}
.copyright{left:91px;top:1166px;font-size:8px;font-style:italic;color:#aaa}
.copyright span{color:var(--gold)}
.social{left:644px;top:1160px;display:flex;gap:3px}
.social span{width:25px;height:25px;border-radius:50%;background:#e4e4e4}
</style>
</head>
<body>

<header class="site-header abs"></header>
<div class="brand abs">
  <div class="brand-name">Vensol<br>Holdings</div>
</div>
<nav class="main-nav abs">
  <a style="left:459px">HOME</a>
  <a style="left:507px">ABOUT</a>
  <a style="left:558px">SERVICES</a>
  <a style="left:619px">WORK</a>
  <a style="left:667px">BLOG</a>
  <a style="left:713px">CONTACT</a>
</nav>

<section class="hero abs" role="img" aria-label="Night skyline of a modern city with lit office towers and light trails"></section>
<div class="hero-caption abs">Vensol Holdings is a new real-estate project operator, structuring urban-rural real-estate investment and development..</div>
<div class="hero-dots abs"><span></span><span></span><span></span><span></span></div>
<div class="hero-rule abs"></div>
<div class="hero-shadow abs"></div>

<section class="welcome abs">
  <h1>Welcome to <em>Vensol Holdings</em></h1>
  <p>VENSOL HOLDINGS, located in Qianhai, China, is a new real-estate project operator, structuring urban-rural real-estate investment and development, and industrial fund investment. The company also invests in supply chain management and supporting infrastructures. To create new spaces and livable cities Vensol Holdings develop win-win strategic partnerships with a number of institutions. Currently cooperating with Tianjing North Lumore, China urban and rural integrated demonstration.</p>
</section>

<div class="news-bar abs"></div>
<div class="news-icon abs"></div>
<div class="news-label abs">Latest <span class="gold-word">News :</span></div>
<div class="news-text abs">Sed accumsan sollicitudin sapien, sit amet adipiscing turpis gravida ac turpis convallis semper..<a>Read More</a></div>
<svg class="news-arrows abs" width="24" height="12" viewBox="0 0 24 12">
  <path d="M6 2 L2 6 L6 10 M18 2 L22 6 L18 10" fill="none" stroke="#555" stroke-width="1.4"/>
</svg>

<section class="projects abs" role="img" aria-label="Dark evening city skyline backdrop"></section>
<div class="project-photo abs" role="img" aria-label="Architectural scale model of residential towers with landscaped grounds"></div>
<svg class="slide-btn abs" style="left:96px" viewBox="0 0 26 26"><circle cx="13" cy="13" r="13" fill="#1a1a1a"/><path d="M15 8 L10 13 L15 18" fill="none" stroke="#fff" stroke-width="2"/></svg>
<svg class="slide-btn abs" style="left:442px" viewBox="0 0 26 26"><circle cx="13" cy="13" r="13" fill="#1a1a1a"/><path d="M11 8 L16 13 L11 18" fill="none" stroke="#fff" stroke-width="2"/></svg>
<h2 class="projects-title abs">Latest <span style="color:var(--gold-light)">Projects</span></h2>
<article class="project-item abs" style="top:710px">
  <h3>Aliquam molestie, mi et imperdiet euismod</h3>
  <p>Dui purus auctor tellus, et interdum lacus lectus et ante.<br>Etiam pretium porttitor lectus, vel ornare neque<br>porta volutpat.</p>
</article>
<article class="project-item abs" style="top:783px">
  <h3>Aliquam molestie, mi et imperdiet euismod</h3>
  <p>Dui purus auctor tellus, et interdum lacus lectus et ante.<br>Etiam pretium porttitor lectus, vel ornare neque<br>porta volutpat.</p>
</article>
<div class="view-more abs">VIEW MORE</div>

<section class="info abs"></section>
<h2 class="info-title abs" style="left:91px">About Us</h2>
<p class="about-text abs">Dui purus auctor tellus, et interdum lacus lectus et ante. Etiam pretium porttitor lectus, vel ornare neque porta volutpat. Sed accumsan sollicitudin sapien, sit amet adipiscing turpis gravida ac. Dui purus auctor tellus, et interdum lacus lectus et ante.Etiam pretium porttitor lectus, vel ornare neque porta volutpat.</p>
<div class="learn-more abs">LEARN MORE</div>

<h2 class="info-title abs" style="left:334px">Our Services</h2>
<ul class="service-list abs">
  <li>Dui purus auctor telluse</li>
  <li>Interdum lacus lectus et ante</li>
  <li>Etiam pretium porttitor lectus</li>
  <li>Sed accumsan sollicitudin sapien</li>
  <li>Sit amet adipiscing turpis gravida ac</li>
  <li>Dui purus auctor tellus</li>
</ul>

<h2 class="info-title abs" style="left:542px">Contact Us</h2>
<div class="field abs" style="left:542px;top:988px;width:211px;height:25px">Name</div>
<div class="field abs" style="left:542px;top:1019px;width:101px;height:25px">Email</div>
<div class="field abs" style="left:652px;top:1019px;width:101px;height:25px">Phone</div>
<div class="field field-msg abs" style="left:542px;top:1050px;width:211px;height:48px">Type Message</div>
<div class="send-btn abs">SEND</div>

<footer class="site-footer abs"></footer>
<div class="copyright abs">Copyright copyright © 2013. <span>Vensol Holdings</span>. All Righr Reserved</div>
<div class="social abs"><span></span><span></span><span></span><span></span></div>

</body>
</html>
```